Allied Health team of Physiotherapists & Occupational Therapists seek a business card design

We have our new logo, we now need our new business cards and stationary. Tidewell: Oedema & Family Clinic is seeking a generic card design to represent our whole team and individual cards for each therapist that incorporates our new logo to communicate our holistic approach that is calming, nuturing, supportive and welcoming.
Our Physiotherapists and Occupational Therapists assess, treat and provide education for people who are at risk of or who have lymphoedema. This is often as a result of treatment for cancer. We provide pre-operative and post-operative management and cancer rehabilitation in our Pilates studio. Our team also consists of Physiotherapists who have a strong interest in pelvic floor and continence management for both men and women.

Target Market(s)

Mainly women health conscious

Industry/Entity Type

Allied Health: Physiotherapy / Occupational Therapy

Contact Information for Business Card

Address: 14 Gallivant Ave Shellharbour Bay 3957 Phone: 84316570 fax: 8431 6578 Email: info@tidewellcareservices.com.au Website: tidewellcareservices.com.au Facebook address: facebook.com/TidewellOedemaAndFamilyCareClinic. Room to write appointments. Individual cards need to have name, office email and individual email and professional details

Requirements
Must have
• Logo as per uploaded documents

```html
<!DOCTYPE html>
<html lang="en">
<head>
<meta charset="utf-8">
<title>Tidewell: Oedema &amp; Family Clinic — Business Cards</title>
<link rel="stylesheet" href="https://fonts.googleapis.com/css2?family=Jost:wght@400;500;600&family=Lato:ital,wght@0,400;1,700&display=swap">
<style>
  :root {
    --stage: #080808;
    --card-cream: #fdf9d6;
    --ink-dark: #2b2b2b;
    --ink-body: #3d3d3d;
    --peach: #f3a37f;
    --coral-light: #f9bb93;
    --coral-deep: #f39576;
    --cream-text: #fff6ea;
  }
  * { box-sizing: border-box; margin: 0; padding: 0; }
  html, body {
    width: 1200px; height: 892px; overflow: hidden;
    background: var(--stage);
  }
  .stage { position: relative; width: 1200px; height: 892px; }

  .card {
    position: absolute; width: 502px; height: 287px;
    box-shadow: 12px 14px 22px rgba(0,0,0,0.55);
    font-family: "Jost", sans-serif;
  }
  .card--front { left: 223px; top: 121px; background: var(--card-cream); }
  .card--back {
    left: 474px; top: 483px;
    background: linear-gradient(90deg, var(--coral-light) 0%, var(--coral-deep) 100%);
    color: var(--cream-text);
  }

  .brand {
    position: absolute; width: 134px; height: 134px;
    display: flex; flex-direction: column; align-items: center; justify-content: center;
    text-align: center; font-family: "Jost", sans-serif; font-weight: 500;
  }
  .brand::before {
    content: ""; position: absolute; inset: 0;
    border: 1.5px solid currentColor; border-radius: 50%;
  }
  .brand__name { font-size: 25px; line-height: 1.1; }
  .brand__tag { font-size: 9.5px; line-height: 1.25; letter-spacing: 0.5px; margin-top: 3px; }
  .card--front .brand { left: 36px; top: 32px; color: var(--peach); }
  .card--back .brand { left: 335px; top: 28px; color: var(--cream-text); }

  .person { position: absolute; right: 17px; top: 37px; text-align: right; }
  .person__name {
    font-family: "Lato", sans-serif; font-style: italic; font-weight: 700;
    font-size: 26px; color: var(--ink-dark); letter-spacing: 0.2px;
  }
  .person__role { font-size: 13px; color: var(--ink-body); margin-top: 4px; }

  .services {
    position: absolute; left: 18px; top: 216px;
    font-size: 13.5px; font-weight: 500; line-height: 18px; color: var(--ink-body);
    list-style: none;
  }

  .contacts {
    position: absolute; left: 38px; top: 67px; list-style: none;
    font-size: 14px; letter-spacing: 0.3px; line-height: 20px;
  }
  .contacts li { display: flex; align-items: center; gap: 5px; }
  .contacts li.phone { letter-spacing: 1.2px; }
  .contacts svg { width: 15px; height: 15px; flex: none; }

  .appointment {
    position: absolute; left: 38px; top: 205px; font-size: 15px;
  }
  .appointment__line { letter-spacing: 1px; opacity: 0.9; }
  .website { position: absolute; left: 38px; top: 244px; font-size: 15px; }
</style>
</head>
<body>
<main class="stage">

  <section class="card card--front" aria-label="Business card front">
    <div class="brand">
      <span class="brand__name">Tidewell</span>
      <span class="brand__tag">Oedema &amp;<br>Family Clinic</span>
    </div>
    <div class="person">
      <h1 class="person__name">Maren Ashby</h1>
      <p class="person__role">Physiotherapist</p>
    </div>
    <ul class="services">
      <li>Lymphoedema &amp; Oncology Rehabilitation</li>
      <li>Continence &amp; Pelvic Floor</li>
    </ul>
  </section>

  <section class="card card--back" aria-label="Business card back">
    <ul class="contacts">
      <li class="phone">
        <svg viewBox="0 0 16 16" aria-hidden="true"><circle cx="8" cy="8" r="7" fill="none" stroke="currentColor" stroke-width="1.3"/><path d="M5.3 4.6l1.3-.2.7 1.7-.8.7a5 5 0 0 0 2.6 2.6l.7-.8 1.7.7-.2 1.3c-3.3.3-6.3-2.7-6-6z" fill="currentColor"/></svg>
        8431 6570
      </li>
      <li class="phone">
        <svg viewBox="0 0 16 16" aria-hidden="true"><circle cx="8" cy="8" r="7" fill="none" stroke="currentColor" stroke-width="1.3"/><rect x="4.5" y="6.5" width="7" height="4.5" rx="0.6" fill="currentColor"/><rect x="6" y="4.3" width="4" height="2.4" fill="none" stroke="currentColor" stroke-width="1"/></svg>
        8431 6578
      </li>
      <li>
        <svg viewBox="0 0 16 16" aria-hidden="true"><circle cx="8" cy="8" r="7" fill="none" stroke="currentColor" stroke-width="1.3"/><rect x="4.3" y="5.3" width="7.4" height="5.4" rx="0.6" fill="currentColor"/><path d="M4.5 5.6L8 8.4l3.5-2.8" fill="none" stroke="var(--coral-light)" stroke-width="0.9"/></svg>
        info@tidewellcareservices.com.au
      </li>
      <li>
        <svg viewBox="0 0 16 16" aria-hidden="true"><circle cx="8" cy="8" r="7" fill="none" stroke="currentColor" stroke-width="1.3"/><path d="M8 12.3s-3-3.1-3-5.2a3 3 0 0 1 6 0c0 2.1-3 5.2-3 5.2z" fill="currentColor"/><circle cx="8" cy="7.1" r="1.1" fill="var(--coral-light)"/></svg>
        14 Gallivant Ave, Shellharbour Bay 3957
      </li>
    </ul>
    <div class="brand">
      <span class="brand__name">Tidewell</span>
      <span class="brand__tag">Oedema &amp;<br>Family Clinic</span>
    </div>
    <p class="appointment">Next Appointment <span class="appointment__line">.........................</span></p>
    <p class="website">www.tidewellcareservices.com.au (Book Online)</p>
  </section>

</main>
</body>
</html>
```